Brimlow OrthoLink IT Inc. new website

i need a website for my company which is dedicated to installation and service of computer systems in Dental Offices. I would like for it to encompass a technology feel and professional look. The company deals with all aspects of technology like, Audio Visual, computer systems and networks, Cloud services like data backup, data center. We provide manage services, support and services to Dental Professionals.
Updates

Looking for a Technology font but professional look Added Wednesday, April 20, 2016

Target Market(s)

Dental, Dentist

Industry/Entity Type

Dental

Number of Pages Required

5+ page

Font styles to use
Other font styles liked:
• Futuristic or Techy

Colors
0255a3
ec1f27

Requirements
Must have
• Tabs
Nice to have
• Have no idea maybe some suggestion on your part may help
Should not have
• A professional feel but have a techy look

```html
<!DOCTYPE html>
<html lang="en">
<head>
<meta charset="utf-8">
<title>Brimlow OrthoLink IT Inc.</title>
<link rel="stylesheet" href="https://fonts.googleapis.com/css2?family=Lato:wght@700;900&family=Open+Sans:wght@400;600;700&family=Raleway:wght@400;500;700&display=swap">
<style>
:root{
  --brand:#0255a3;
  --brand-dark:#024a8e;
  --ink:#111111;
  --text:#666666;
  --muted:#8a8a8a;
  --light:#ececec;
  --white:#ffffff;
  --footer:#2b2b2b;
  --footer-line:#444444;
  --black:#0a0a0a;
}
*{box-sizing:border-box;margin:0;padding:0}
html,body{width:1200px;height:2744px;overflow:hidden}
body{font-family:"Open Sans",Arial,sans-serif;color:var(--text);background:var(--white);position:relative}
.wrap{position:absolute;left:0;width:1200px}

/* header */
.site-header{top:0;height:119px;background:var(--white)}
.brand{position:absolute;left:79px;top:30px;display:flex;align-items:center;gap:14px}
.brand-mark{width:40px;height:40px;background:var(--brand);border-radius:6px}
.brand-name{font-family:"Lato",sans-serif;font-weight:900;font-size:30px;color:var(--brand);line-height:1.05;letter-spacing:-.3px}
.contact-bar{position:absolute;top:27px;left:589px;display:flex;align-items:center}
.contact-item{display:flex;align-items:center;gap:16px}
.contact-icon{width:58px;height:58px;border:2px solid var(--brand);border-radius:50%;display:flex;align-items:center;justify-content:center}
.contact-phone{font-family:"Open Sans",sans-serif;font-weight:600;font-size:26px;color:var(--brand)}
.contact-mail{font-size:19px;color:var(--brand)}
.contact-divider{width:1px;height:52px;background:#d6d6d6;margin:0 18px 0 22px}

/* navigation */
.main-nav{top:119px;height:57px;background:var(--brand)}
.main-nav ul{list-style:none;position:relative;height:57px}
.main-nav li{position:absolute;top:0;height:57px;line-height:57px;font-size:19px;color:var(--white);text-transform:uppercase}
.main-nav li.active{background:var(--black);width:123px;text-align:center}

/* hero */
.hero{top:176px;height:570px}
.hero-photo{position:absolute;inset:0;background:linear-gradient(90deg,#d9d9d9 0%,#e8e9ea 35%,#eef0f2 60%,#f3f4f5 100%)}
.hero-copy{position:absolute;right:95px;top:130px;text-align:right}
.hero-title{font-family:"Lato",sans-serif;font-weight:900;font-size:44px;line-height:62px;color:var(--ink)}
.hero-text{font-size:20px;line-height:31px;color:#222;margin-top:12px}
.btn{display:inline-block;font-family:"Lato",sans-serif;font-weight:900;text-transform:uppercase;text-align:center}
.btn-hero{width:203px;height:62px;line-height:62px;background:var(--brand);color:var(--white);font-size:24px;border-radius:4px;margin-top:20px}

/* services */
.services{top:746px;height:485px;background:var(--light);text-align:center}
.section-title{font-family:"Raleway",sans-serif;font-weight:400;text-transform:uppercase;color:var(--ink)}
.section-title span{color:var(--brand)}
.services .section-title{font-size:48px;margin-top:50px}
.service{position:absolute;top:132px;width:340px;text-align:center}
.service-icon{width:124px;height:124px;border:2px solid var(--brand);border-radius:50%;margin:0 auto;display:flex;align-items:center;justify-content:center}
.service-title{font-family:"Raleway",sans-serif;font-weight:500;font-size:23px;line-height:33px;color:var(--ink);text-transform:uppercase;margin-top:18px}
.service-text{font-size:15.5px;line-height:25px;color:var(--muted);margin-top:4px;padding:0 10px}

/* welcome */
.welcome{top:1231px;height:393px;background:var(--white)}
.welcome-copy{position:absolute;left:79px;top:52px;width:605px}
.welcome .section-title{font-size:43px}
.welcome-copy p{font-size:15.5px;line-height:25px;color:var(--text);margin-top:14px}
.welcome-copy p + p{margin-top:24px}
.read-more{display:block;margin-top:22px;font-family:"Raleway",sans-serif;font-weight:700;font-size:20px;color:var(--brand)}
.video-screen{position:absolute;left:759px;top:59px;width:362px;height:292px;background:linear-gradient(180deg,#1b1b1b 0%,#1b1b1b 72%,#cfd1d3 72%,#b9bbbe 100%);border-radius:6px}

/* support band */
.support{top:1624px;height:313px;text-align:center}
.support-photo{position:absolute;inset:0;background:linear-gradient(90deg,#2a62a4 0%,#3a72b3 50%,#2f68aa 100%)}
.support-inner{position:relative}
.support .section-title{color:var(--white);font-size:48px;margin-top:48px}
.support p{color:var(--white);font-size:15.5px;line-height:25px;width:820px;margin:10px auto 0}
.btn-support{width:218px;height:55px;line-height:55px;background:var(--white);color:var(--ink);font-size:22px;border-radius:4px;margin-top:38px}

/* contact + testimonials */
.engage{top:1937px;height:479px;background:var(--light)}
.engage .section-title{font-size:37px}
.contact-form{position:absolute;left:77px;top:62px;width:470px}
.field{display:block;width:468px;height:41px;background:var(--white);border:1px solid #cfcfcf;font-size:15px;color:#555;padding:0 8px;line-height:39px;margin-top:12px}
.field.message{height:92px;line-height:26px;padding-top:6px}
.btn-submit{position:absolute;left:0;top:316px;width:135px;height:41px;line-height:41px;background:var(--brand);color:var(--white);font-family:"Raleway",sans-serif;font-weight:500;font-size:21px}
.testimonials{position:absolute;left:642px;top:62px;width:480px}
.testimonial{position:absolute;left:0;width:480px}
.client-photo{position:absolute;left:0;top:0;width:124px;height:124px;border-radius:50%;border:3px solid var(--brand)}
.testimonial p{position:absolute;left:139px;top:4px;width:340px;font-size:15.5px;line-height:28px;color:var(--text)}
.client-name{display:block;font-size:13px;font-weight:700;color:var(--brand);text-transform:uppercase;margin-top:2px}

/* footer */
.site-footer{top:2416px;height:328px;background:var(--footer);color:#bdbdbd}
.footer-col{position:absolute;top:28px;width:250px}
.footer-col h4{font-family:"Raleway",sans-serif;font-weight:500;font-size:22px;color:var(--white);margin-bottom:14px}
.link-list{list-style:none}
.link-list li{font-size:15px;line-height:31px;color:#9a9a9a;display:flex;align-items:center;gap:8px}
.link-list li.current{color:var(--white)}
.news-item{font-size:15px;line-height:23px;color:#e0e0e0;margin-bottom:24px}
.news-item time{display:block}
.newsletter p{font-size:14px;color:#e0e0e0;margin-bottom:16px}
.news-field{width:234px;height:37px;border:1px solid #cfcfcf;font-size:15px;color:#e0e0e0;padding:0 8px;line-height:35px;margin-bottom:10px}
.btn-subscribe{width:160px;height:40px;line-height:40px;background:var(--brand);color:var(--white);font-family:"Raleway",sans-serif;font-weight:500;font-size:20px;text-align:center;margin-top:6px}
.info-line{display:flex;gap:10px;font-size:15px;line-height:23px;color:#e0e0e0;margin-bottom:12px}
.info-phone{font-weight:700;font-size:22px;color:var(--white)}
.social{display:flex;gap:16px;margin-top:10px}
.social span{width:48px;height:48px;border-radius:50%;border:2px solid var(--white);display:block}
.footer-bottom{position:absolute;left:79px;top:274px;width:1042px;border-top:1px solid var(--footer-line);text-align:center;font-size:15px;color:#e0e0e0;padding-top:16px}
.footer-bottom b{color:var(--white)}
</style>
</head>
<body>

<header class="wrap site-header">
  <div class="brand">
    <span class="brand-mark"></span>
    <span class="brand-name">Brimlow<br>OrthoLink IT</span>
  </div>
  <div class="contact-bar">
    <div class="contact-item">
      <span class="contact-icon">
        <svg width="26" height="26" viewBox="0 0 24 24"><path d="M6.6 10.8a15 15 0 0 0 6.6 6.6l2.2-2.2a1 1 0 0 1 1-.25 11.4 11.4 0 0 0 3.6.57 1 1 0 0 1 1 1V20a1 1 0 0 1-1 1A17 17 0 0 1 3 4a1 1 0 0 1 1-1h3.5a1 1 0 0 1 1 1c0 1.25.2 2.45.57 3.57a1 1 0 0 1-.25 1z" fill="#0255a3"/></svg>
      </span>
      <span class="contact-phone">555 014 2290</span>
    </div>
    <span class="contact-divider"></span>
    <div class="contact-item">
      <span class="contact-icon">
        <svg width="26" height="20" viewBox="0 0 26 20"><rect x="1.5" y="1.5" width="23" height="17" rx="2" fill="none" stroke="#0255a3" stroke-width="2"/><path d="M2 3l11 8 11-8" fill="none" stroke="#0255a3" stroke-width="2"/></svg>
      </span>
      <span class="contact-mail">info@brimlowortholink.com</span>
    </div>
  </div>
</header>

<nav class="wrap main-nav">
  <ul>
    <li class="active" style="left:77px">Home</li>
    <li style="left:232px">About</li>
    <li style="left:368px">Services</li>
    <li style="left:523px">Support</li>
    <li style="left:677px">Client</li>
    <li style="left:812px">Blog</li>
    <li style="left:931px">Contact</li>
  </ul>
</nav>

<section class="wrap hero">
  <div class="hero-photo" role="img" aria-label="Dental professional holding a tablet in a bright modern dental treatment room"></div>
  <div class="hero-copy">
    <h1 class="hero-title">TECHNOLOGY FOR<br>BEST PRACTICE</h1>
    <p class="hero-text">f you view technology as an expense rather than<br>an investment, you haven't worked with us.</p>
    <span class="btn btn-hero">Contact Us</span>
  </div>
</section>

<section class="wrap services">
  <h2 class="section-title">Our <span>Services</span></h2>
  <div class="service" style="left:64px">
    <div class="service-icon">
      <svg width="66" height="58" viewBox="0 0 66 58"><rect x="3" y="3" width="60" height="40" rx="3" fill="none" stroke="#0255a3" stroke-width="4"/><rect x="20" y="13" width="26" height="18" fill="#0255a3"/><path d="M30 17v10l8-5z" fill="#fff"/><path d="M26 43l-3 10h20l-3-10" fill="#0255a3"/></svg>
    </div>
    <h3 class="service-title">Audio Visual</h3>
    <p class="service-text">Lorem Ipsum is simply dummy text of the printing and typesetting industry. Lorem Ipsum has been the industry.</p>
  </div>
  <div class="service" style="left:430px">
    <div class="service-icon">
      <svg width="72" height="62" viewBox="0 0 72 62"><rect x="2" y="18" width="26" height="18" rx="2" fill="none" stroke="#0255a3" stroke-width="3"/><path d="M0 40h30" stroke="#0255a3" stroke-width="3"/><path d="M28 27h10M38 7v48M38 7h8M38 22h8M38 38h8M38 55h8" stroke="#0255a3" stroke-width="3" fill="none"/><rect x="46" y="2" width="20" height="11" rx="2" fill="none" stroke="#0255a3" stroke-width="3"/><rect x="46" y="17" width="20" height="11" rx="2" fill="none" stroke="#0255a3" stroke-width="3"/><rect x="46" y="33" width="20" height="11" rx="2" fill="none" stroke="#0255a3" stroke-width="3"/><rect x="46" y="49" width="20" height="11" rx="2" fill="none" stroke="#0255a3" stroke-width="3"/></svg>
    </div>
    <h3 class="service-title">Computer Systems and<br>Networks</h3>
    <p class="service-text">Lorem Ipsum is simply dummy text of the printing and typesetting industry. Lorem Ipsum has been the industry.</p>
  </div>
  <div class="service" style="left:796px">
    <div class="service-icon">
      <svg width="74" height="60" viewBox="0 0 74 60"><path d="M18 44a14 14 0 0 1 0-28 18 18 0 0 1 34-2 13 13 0 0 1 10 20" fill="none" stroke="#0255a3" stroke-width="4"/><ellipse cx="50" cy="34" rx="12" ry="5" fill="#0255a3"/><path d="M38 34v16c0 3 5 5 12 5s12-2 12-5V34" fill="#0255a3"/><path d="M38 42c0 3 5 5 12 5s12-2 12-5" stroke="#fff" stroke-width="2" fill="none"/><circle cx="63" cy="50" r="8" fill="#fff" stroke="#0255a3" stroke-width="3"/><path d="M63 45v5h4" stroke="#0255a3" stroke-width="2.5" fill="none"/></svg>
    </div>
    <h3 class="service-title">Cloud Services of Data<br>Backup</h3>
    <p class="service-text">Lorem Ipsum is simply dummy text of the printing and typesetting industry. Lorem Ipsum has been the industry.</p>
  </div>
</section>

<section class="wrap welcome">
  <div class="welcome-copy">
    <h2 class="section-title">Welcome to <span>Brimlow OrthoLink IT</span></h2>
    <p>Lorem Ipsum is simply dummy text of the printing and typesetting industry. Lorem Ipsum has been the industry's standard dummy text ever since the 1500s, when an unknown printer took a galley of type and scrambled it to make a type specimen book.</p>
    <p>Lorem Ipsum is simply dummy text of the printing and typesetting industry. Lorem Ipsum has been the industry</p>
    <span class="read-more">READ MORE »</span>
  </div>
  <div class="video-screen" role="img" aria-label="Desktop screen showing an introduction video filmed in a dental clinic"></div>
</section>

<section class="wrap support">
  <div class="support-photo" role="img" aria-label="Dental treatment room under a blue tint"></div>
  <div class="support-inner">
    <h2 class="section-title">Support with us</h2>
    <p>Lorem Ipsum is simply dummy text of the printing and typesetting industry. Lorem Ipsum has been the industry's standard dummy text ever since the 1500s, when an unknown printer took a galley.</p>
    <span class="btn btn-support">Get Support</span>
  </div>
</section>

<section class="wrap engage">
  <div class="contact-form">
    <h2 class="section-title">Get in touch <span>with us</span></h2>
    <span class="field">Enter Name</span>
    <span class="field">Enter Email</span>
    <span class="field">Enter Contact No.</span>
    <span class="field message">Message</span>
    <span class="btn-submit" style="text-align:center">SUBMIT</span>
  </div>
  <div class="testimonials">
    <h2 class="section-title">Client <span>Testimonial</span></h2>
    <div class="testimonial" style="top:54px">
      <div class="client-photo" role="img" aria-label="Portrait of a client" style="background:linear-gradient(180deg,#c9c3bb,#9e9a96)"></div>
      <p>Lorem Ipsum is simply dummy text of the printing and typesetting industry. Lorem Ipsum has been the industry's standard dummy text.<span class="client-name">- Client Name</span></p>
    </div>
    <div class="testimonial" style="top:212px">
      <div class="client-photo" role="img" aria-label="Portrait of a client" style="background:linear-gradient(180deg,#d9d9d9,#7f8793)"></div>
      <p>Lorem Ipsum is simply dummy text of the printing and typesetting industry. Lorem Ipsum has been the industry's standard dummy text.<span class="client-name">- Client Name</span></p>
    </div>
  </div>
</section>

<footer class="wrap site-footer">
  <div class="footer-col" style="left:79px">
    <h4>Useful Links</h4>
    <ul class="link-list">
      <li class="current"><svg width="14" height="12" viewBox="0 0 14 12"><path d="M1 1l5 5-5 5M7 1l5 5-5 5" stroke="currentColor" stroke-width="2" fill="none"/></svg>Home</li>
      <li><svg width="14" height="12" viewBox="0 0 14 12"><path d="M1 1l5 5-5 5M7 1l5 5-5 5" stroke="currentColor" stroke-width="2" fill="none"/></svg>About</li>
      <li><svg width="14" height="12" viewBox="0 0 14 12"><path d="M1 1l5 5-5 5M7 1l5 5-5 5" stroke="currentColor" stroke-width="2" fill="none"/></svg>Services</li>
      <li><svg width="14" height="12" viewBox="0 0 14 12"><path d="M1 1l5 5-5 5M7 1l5 5-5 5" stroke="currentColor" stroke-width="2" fill="none"/></svg>Support</li>
      <li><svg width="14" height="12" viewBox="0 0 14 12"><path d="M1 1l5 5-5 5M7 1l5 5-5 5" stroke="currentColor" stroke-width="2" fill="none"/></svg>News</li>
      <li><svg width="14" height="12" viewBox="0 0 14 12"><path d="M1 1l5 5-5 5M7 1l5 5-5 5" stroke="currentColor" stroke-width="2" fill="none"/></svg>Contact</li>
    </ul>
  </div>
  <div class="footer-col" style="left:349px">
    <h4>Latest News</h4>
    <p class="news-item">Lorem Ipsum is simply dummy text of the printing.<time>21 April 2016</time></p>
    <p class="news-item">Lorem Ipsum is simply dummy text of the printing.<time>21 April 2016</time></p>
  </div>
  <div class="footer-col newsletter" style="left:620px">
    <h4>Newsletter</h4>
    <p>Subscribe to stay on Brimlow OrthoLink IT.</p>
    <div class="news-field">Enter Name</div>
    <div class="news-field">Enter Email</div>
    <div class="btn-subscribe">SUBSCRIBE</div>
  </div>
  <div class="footer-col" style="left:891px">
    <h4>Contact Info</h4>
    <div class="info-line"><svg width="16" height="22" viewBox="0 0 16 22"><path d="M8 1a7 7 0 0 1 7 7c0 5-7 13-7 13S1 13 1 8a7 7 0 0 1 7-7z" fill="#fff"/><circle cx="8" cy="8" r="2.6" fill="#2b2b2b"/></svg><span>Lorem Ipsum is simply dummy text of the printing.</span></div>
    <div class="info-line info-phone"><svg width="20" height="20" viewBox="0 0 24 24"><path d="M6.6 10.8a15 15 0 0 0 6.6 6.6l2.2-2.2a1 1 0 0 1 1-.25 11.4 11.4 0 0 0 3.6.57 1 1 0 0 1 1 1V20a1 1 0 0 1-1 1A17 17 0 0 1 3 4a1 1 0 0 1 1-1h3.5a1 1 0 0 1 1 1c0 1.25.2 2.45.57 3.57a1 1 0 0 1-.25 1z" fill="#fff"/></svg>555 014 2290</div>
    <div class="info-line"><svg width="18" height="14" viewBox="0 0 26 20"><rect x="1.5" y="1.5" width="23" height="17" rx="2" fill="none" stroke="#fff" stroke-width="2.5"/><path d="M2 3l11 8 11-8" fill="none" stroke="#fff" stroke-width="2.5"/></svg>info@brimlowortholink.com</div>
    <div class="social" aria-label="Social profiles"><span></span><span></span><span></span></div>
  </div>
  <div class="footer-bottom">© <b>BRIMLOW ORTHOLINK IT</b> - 2016. All Rights Reserved.</div>
</footer>

</body>
</html>
```